Need Help having my business card stand out

I am the owner of Birchway Canine Training and would like for my business cards to stand out. I have been trying to keep designing them myself but I can't get what I have in my head on the card. I will try my best to post templates that I like for inspirations. I want something unique but elegant. I don't want in to look cartoony or cheesy. It needs to pop in a pet shop but also in a coffee shop or gym.

Target Market(s)

Dog owners, Married ,No young kids Jr High school kids and up (maybe kids on the way) Executives, Stay at home moms/wives, Small business owners

Industry/Entity Type

Dog Training

Contact Information for Business Card

Lowell Spratt, 281-904-3376, info@birchwaycanine.example, www.birchwaycanine.example

Colors

Designer to choose colors to be used in the design.

Requirements
Must have
• my logo
Should not have
• Cursive lettering

```html
<!DOCTYPE html>
<html lang="en">
<head>
<meta charset="utf-8">
<title>Birchway Canine Training – Business Card</title>
<link rel="stylesheet" href="https://fonts.googleapis.com/css2?family=Open+Sans:wght@300;400;600;700&display=swap">
<style>
  :root {
    --page: #c7d9e1;
    --blue-light: #2b86d0;
    --blue-mid: #1c6fbd;
    --blue-deep: #145aa3;
    --navy: #0d2c63;
    --band: rgba(10, 60, 130, 0.22);
    --tag-faint: #4f9be0;
    --white: #ffffff;
  }
  * { box-sizing: border-box; margin: 0; padding: 0; }
  html, body { width: 1200px; height: 800px; overflow: hidden; }
  body {
    background: var(--page);
    font-family: "Open Sans", Arial, sans-serif;
    display: flex;
    align-items: center;
    justify-content: center;
    gap: 40px;
  }
  .card {
    position: relative;
    width: 525px;
    height: 300px;
    overflow: hidden;
    background: linear-gradient(125deg, var(--blue-deep) 0%, var(--blue-light) 45%, var(--blue-mid) 70%, var(--blue-deep) 100%);
    box-shadow: 0 10px 24px rgba(20, 50, 80, 0.18);
    color: var(--white);
  }
  /* logo side */
  .card__band {
    position: absolute;
    left: 0; right: 0;
    background: var(--band);
  }
  .card--front .card__band { top: 196px; height: 56px; }
  .brand {
    position: absolute;
    top: 92px; left: 0; right: 0;
    display: flex;
    align-items: center;
    justify-content: center;
    gap: 12px;
  }
  .brand__mark {
    width: 26px; height: 26px;
    background: var(--navy);
  }
  .brand__name {
    font-weight: 700;
    font-size: 27px;
    color: var(--navy);
    letter-spacing: 0.2px;
  }
  .rule {
    position: absolute;
    height: 2px;
    width: 52px;
    background: var(--navy);
    opacity: 0.55;
  }
  .rule--left { left: 28px; top: 168px; }
  .rule--right { right: 28px; top: 72px; }
  .tagline {
    position: absolute;
    font-weight: 700;
    font-size: 13px;
    letter-spacing: 2.6px;
    text-transform: uppercase;
  }
  .card--front .tagline {
    top: 215px; left: 0; right: 0;
    text-align: center;
    color: var(--navy);
  }
  /* contact side */
  .card--back .card__band { top: 28px; height: 44px; }
  .card--back .tagline {
    top: 42px; right: 30px;
    color: var(--tag-faint);
  }
  .contact-strip {
    position: absolute;
    left: 300px; top: 96px;
    width: 24px; height: 150px;
    background: var(--navy);
    display: flex;
    flex-direction: column;
    justify-content: flex-end;
    align-items: center;
    gap: 9px;
    padding-bottom: 12px;
  }
  .contact-strip svg { width: 12px; height: 12px; }
  .contact-list {
    position: absolute;
    left: 340px; top: 120px;
    list-style: none;
    font-size: 11px;
    line-height: 21px;
    color: var(--white);
  }
  .person {
    position: absolute;
    left: 36px; top: 212px;
  }
  .person__name { font-size: 22px; font-weight: 300; line-height: 1; }
  .person__name strong { font-weight: 700; }
  .person__role { font-size: 17px; font-weight: 300; margin-top: 2px; }
</style>
</head>
<body>

  <section class="card card--front" aria-label="Business card, logo side">
    <div class="card__band"></div>
    <span class="rule rule--left"></span>
    <span class="rule rule--right"></span>
    <div class="brand">
      <span class="brand__mark"></span>
      <span class="brand__name">Birchway Canine Training</span>
    </div>
    <p class="tagline">Your dog trainer for life</p>
  </section>

  <section class="card card--back" aria-label="Business card, contact side">
    <div class="card__band"></div>
    <p class="tagline">Your dog trainer for life</p>

    <div class="contact-strip">
      <svg viewBox="0 0 12 12" aria-hidden="true"><path fill="#fff" d="M6 0.5a3.8 3.8 0 0 0-3.8 3.8C2.2 7.2 6 11.5 6 11.5s3.8-4.3 3.8-7.2A3.8 3.8 0 0 0 6 .5zm0 5.2a1.4 1.4 0 1 1 0-2.8 1.4 1.4 0 0 1 0 2.8z"/></svg>
      <svg viewBox="0 0 12 12" aria-hidden="true"><path fill="#fff" d="M2.5 1h2l1 2.6-1.3 1a6.5 6.5 0 0 0 3.2 3.2l1-1.3 2.6 1v2A1.5 1.5 0 0 1 9.5 11 8.5 8.5 0 0 1 1 2.5 1.5 1.5 0 0 1 2.5 1z"/></svg>
      <svg viewBox="0 0 12 12" aria-hidden="true"><rect x="0.8" y="2.5" width="10.4" height="7" fill="#fff"/><path d="M1 2.8l5 3.8 5-3.8" fill="none" stroke="#0d2c63" stroke-width="1"/></svg>
      <svg viewBox="0 0 12 12" aria-hidden="true"><g fill="none" stroke="#fff" stroke-width="1"><circle cx="6" cy="6" r="5"/><ellipse cx="6" cy="6" rx="2.2" ry="5"/><path d="M1 6h10M2 3.5h8M2 8.5h8"/></g></svg>
    </div>

    <ul class="contact-list">
      <li>000 Alder Row, Suite 300, Fenwick, US 0000</li>
      <li>281-904-3376</li>
      <li>info@birchwaycanine.example</li>
      <li>www.birchwaycanine.example</li>
    </ul>

    <div class="person">
      <p class="person__name"><strong>Lowell</strong> Spratt</p>
      <p class="person__role">Founder</p>
    </div>
  </section>

</body>
</html>
```